Website development company website

ABOUT COMPANY
Hi everyone! We're a Melbourne, Australia website development company in a need of a website design that will make online store merchants want to engage our services.
We specialise exclusively in Torvista e-commerce platform (https://torvista-platform.example/). What distinguishes our business from competition is that rather than designing and building brand new websites, we offer development, support and maintenance services to established websites. Maintenance and Support are the keywords representing our business.
Our potential clients are people with broken, slow and underperforming Torvista installations who need assistance getting their websites up and making sales. Our website must pass the message that we can help, and provide quick means of making contact.
DESIGN
Overall, we're looking for a slick, clean, airy, conservative design. No need to do anything crazy, try to stick to what's "standard" in website design these days and make it easy on all of us. The website is unlikely to be updated too often so it needs to look attractive and fresh first time over and after a year, too.
Attached is our new logo, which you'll be able to take the basic idea from, the colors and fonts. Though, don't use the fonts from the logo in the website, stick to the standard widely supported fonts. Additional use of Google fonts is fine.
Don't overdo it with colors, stick to conservative basic color set and only use the colors from the log for accents like headings etc. Please, don't be tempted to use the blue and orange as background of whole blocks, other than perhaps footer. Thanks.
For the images used, I'd like to stay away from a design studio/digital agency feel and lean more towards professional support and maintenance services. I'm thinking images of content merchants doing their job. Something along the lines of "We'll be taking care of the website so that you only need to care about the business".
Some ideas I like:
http://www.plumframe-pics.example/detail/photo/portrait-of-confident-male-design-professional-royalty-free-image/572048163
http://www.plumframe-pics.example/detail/photo/designer-taking-picture-of-hat-high-res-stock-photography/839207514
http://www.plumframe-pics.example/detail/photo/woman-packaging-pottery-royalty-free-image/216684093
Images of colorful shopping bags and shopping carts are over the top and not serious enough. Instead of images matching Online Shopping, I'd try going more for Stability, Reliability, Performance.
Our existing website is http://www.bravuln.example. Please, don't take design ideas from it, but it will give you a picture of the structure of our new website and content that's going to be used initially.
If you could include a basic icon set to use throughout the website, that would be great. If the icons could match our logo (attached), it would be a big plus.
ALL PAGES
Every page must contain clearly visible phone number (1300 648 907) and a Contact Us Now button, which opens an AJAX driven popup form with Name, Email, Phone and Message to be sent through.
To start with, main menu items will be Torvista, Portfolio, Contact.
At the bottom of each page, please, include a newsletter subscription form with text Subscribe to Torvista Support and Security Updates.
For the footer, I'd like to see a logo strip with the following logos in grayscale (no need to link anywhere): Torvista, QRX, DataVane, NCB. You'll find the logos on Google Images.
Standard footer columns follow. Here, I'd like to see logos in color: Torvista Certified Developer, Torvista Ceritified Solution Provider. Again, the logos are on Google Images.
No social media logos/links necessary anywhere on the website.
...and then the copyright line.
FRONT PAGE
Large slider with images that would appeal to our target audience. Keywords here would be Torvista System Audit, Torvista Performance Optimisation, Torvista Website Emergency Recovery, Torvista Development Infrastructure Hosting. We'll have a static page created for each of these to link to.
In a corner of the slider, or on the edge, can I have an overlay with logos in color (same as footer): Torvista Certified Developer, Torvista Ceritified Solution Provider.
Underneath, a number of blocks, each with an image and teaser that we'll use to link to various pages throughout the website.
PORTFOLIO PAGE
I'm thinking a single long page with a block per client, which will contain project name, description from us and a testimonial from client. Also, each block will contain a single large screenshot. No gallery or slideshow is necessary here, just one image per project.
I'll leave the layout up to you, but try to put yourself in the shoes of a potential client reviewing our past work by simply scrolling down this one page.
CONTACT US PAGE
Separate page with the same form as above, phone number (1300 648 907), email address (support@kavreo.example), address (Suite 42, Level 3|8 Wattlebrook Lane|Fernvale Heights VIC 3999), and a grayscale Google Map.
CODING UP
Coding up into static HTML/CSS/JS is equally important as the design itself. We're a website development company, we'll be integrating the theme. We will spot any issues and we will point them out.
Coded up design must be fully responsive. Enough said.
To be able to create any content in future, we'd like one extra page coded up with samples of all themed elements, lists, forms, buttons, 2, 3, 4-column layout, alerts, icons, etc. This page does not need to be designed, only coded up.
The design will be integrated into Drupal using Twig. If possible at all, try to keep it in mind when designing and coding up, and make the integration into a Drupal theme easier for us.
GOOD LUCK!
That's it. Let me know if anything needs clarifying. So far I've had a great experience with ArtFlockly. I don't doubt some great designs will emerge. Clever ideas are highly appreciated, but also make it clear you've read and followed the points in this brief. Cheers, Tom

```html
<!DOCTYPE html>
<html lang="en">
<head>
<meta charset="utf-8">
<title>Kavreo Commerce – Torvista Support &amp; Maintenance</title>
<link rel="stylesheet" href="https://fonts.googleapis.com/css2?family=Roboto:wght@300;400;500;700&display=swap">
<style>
:root{
  --orange:#ee8a2a;
  --blue:#0d3c73;
  --blue-mid:#154b8a;
  --ink:#333;
  --muted:#777;
  --light:#f4f4f4;
  --line:#e3e3e3;
  --footer:#1f2022;
  --white:#fff;
}
*{margin:0;padding:0;box-sizing:border-box}
html,body{width:672px;height:1200px;overflow:hidden}
body{position:relative;font-family:'Roboto',Arial,sans-serif;color:var(--ink);background:var(--white)}
.abs{position:absolute}

/* header */
.site-header{left:0;top:0;width:672px;height:62px;background:#f6f6f6;border-top:2px solid var(--orange)}
.brand{display:flex;align-items:center;gap:6px}
.brand-mark{width:22px;height:26px;background:var(--orange);border-radius:2px}
.brand-name{font-size:20px;font-weight:700;color:var(--blue);letter-spacing:-.3px}
.main-nav{left:225px;top:28px;display:flex;gap:14px;font-size:7px;color:var(--ink)}
.main-nav .sep{width:2px;height:2px;background:#333;border-radius:50%;margin-top:3px}
.header-phone{left:483px;top:16px;font-size:15px;font-weight:300;color:var(--muted)}
.header-phone b{color:var(--orange);font-weight:300}
.header-icons{left:580px;top:16px;display:flex;gap:5px}
.header-icons span{width:15px;height:15px;border-radius:50%;background:var(--blue);display:flex;align-items:center;justify-content:center}
.header-note{left:448px;top:39px;font-size:6.5px;color:var(--muted)}
.header-note a{color:var(--blue);font-weight:500;text-decoration:none}

/* hero */
.hero{left:0;top:62px;width:672px;height:272px;overflow:hidden}
.hero-photo{position:absolute;inset:0;background:
  radial-gradient(ellipse 150px 110px at 330px 110px,rgba(235,235,238,.75),rgba(235,235,238,0) 70%),
  radial-gradient(ellipse 180px 140px at 560px 150px,rgba(240,236,232,.8),rgba(240,236,232,0) 70%),
  radial-gradient(ellipse 260px 120px at 110px 260px,rgba(170,110,70,.75),rgba(170,110,70,0) 70%),
  linear-gradient(100deg,#4a4037 0%,#7d6f62 30%,#a9a19a 55%,#cfcac4 80%,#bdb4ab 100%)}
.hero-title{left:55px;top:92px;font-size:23px;font-weight:500;color:var(--white)}
.hero-sub{left:55px;top:130px;font-size:16px;font-weight:400;color:var(--white);line-height:24px}
.hero-sub span{font-weight:300}
.hero-dots{left:56px;top:191px;display:flex;gap:7px}
.hero-dots span{width:4px;height:4px;border-radius:50%;background:rgba(255,255,255,.5)}
.hero-dots span:first-child{background:var(--white)}
.hero-badges{left:570px;top:222px;display:flex;gap:4px}
.hero-badges span{width:22px;height:40px;background:rgba(220,220,220,.8);border-radius:2px}

/* welcome */
.welcome{left:55px;top:356px;width:225px}
.welcome h2{font-size:14px;font-weight:300;color:#444;line-height:19px}
.welcome h2 em{font-style:normal;color:var(--orange);font-weight:400}
.welcome p{font-size:6.4px;color:var(--muted);line-height:10px;margin-top:5px}
.welcome ul{list-style:none;margin-top:8px}
.welcome li{font-size:8.4px;color:var(--blue);display:flex;align-items:center;gap:8px;height:18px}
.welcome li svg{flex:none}
.teaser{top:360px;width:103px;height:123px;background:var(--light)}
.teaser h3{height:28px;background:linear-gradient(var(--blue-mid),var(--blue));color:var(--white);font-size:11px;font-weight:400;display:flex;align-items:center;justify-content:center}
.teaser p{font-size:6.4px;color:var(--muted);line-height:9.2px;text-align:justify;padding:8px 7px 0;height:72px;overflow:hidden}
.teaser a{display:block;text-align:center;font-size:7.5px;color:var(--orange);text-decoration:none}

/* services */
.services{left:0;top:505px;width:672px;height:303px}
.services-accent{position:absolute;inset:0;background:#f6c9a1;clip-path:polygon(0 0,50% 12px,100% 0,100% 100%,50% calc(100% - 18px),0 100%)}
.services-bg{position:absolute;left:0;top:0;width:672px;height:298px;background:
  radial-gradient(ellipse 200px 90px at 330px 60px,rgba(120,110,100,.45),rgba(120,110,100,0) 70%),
  radial-gradient(ellipse 180px 120px at 600px 200px,rgba(130,100,80,.5),rgba(130,100,80,0) 70%),
  linear-gradient(90deg,#2a2a2c,#3e3d3f 50%,#5a5552);clip-path:polygon(0 0,50% 12px,100% 0,100% 100%,50% calc(100% - 18px),0 100%)}
.section-title{width:672px;text-align:center;font-size:15px;font-weight:300}
.section-title b{font-weight:400}
.services .section-title{position:absolute;top:40px;color:var(--white)}
.service-card{top:77px;width:133px;height:182px;background:#dcdcdc;border-top:2px solid var(--orange);text-align:center}
.service-photo{width:80px;height:80px;border-radius:50%;border:3px solid var(--white);margin:13px auto 0;box-shadow:0 1px 3px rgba(0,0,0,.3)}
.service-card h3{font-size:9px;font-weight:500;color:#333;line-height:13px;margin-top:13px;height:28px}
.service-card p{font-size:6.4px;color:#666;line-height:10px;padding:2px 9px 0}

/* clients */
.clients{left:0;top:808px;width:672px}
.clients .section-title{color:#444;margin-top:8px}
.clients .section-title b{color:var(--orange)}
.client-strip{display:flex;gap:5px;margin:10px 0 0 55px}
.client-strip span{width:109px;height:48px;border:1px solid #eee;display:flex;align-items:center;justify-content:center;font-size:16px;font-weight:500;color:#bbb}

/* map */
.map{left:0;top:928px;width:672px;height:104px;background:
  radial-gradient(ellipse 160px 50px at 200px 70px,rgba(205,205,205,.9),rgba(205,205,205,0) 70%),
  radial-gradient(ellipse 220px 40px at 520px 40px,rgba(215,215,215,.8),rgba(215,215,215,0) 70%),
  linear-gradient(170deg,#f0f0f0,#e4e4e4 60%,#ececec)}
.map-pin{left:187px;top:44px}

/* footer */
.site-footer{left:0;top:1032px;width:672px;height:168px;background:var(--footer)}
.newsletter{left:89px;top:1032px;width:494px;height:46px;background:var(--blue);display:flex;align-items:center}
.newsletter h4{font-size:9px;font-weight:400;color:var(--white);margin-left:40px;width:161px}
.newsletter h4 b{font-size:14px;font-weight:400}
.newsletter input{width:218px;height:23px;border:0;background:#3f6a9c;color:#cfd9e6;font:italic 6.5px 'Roboto',Arial,sans-serif;padding-left:10px}
.newsletter input::placeholder{color:#c9d5e3}
.newsletter button{width:34px;height:23px;border:0;background:var(--orange);color:var(--white);font:400 11px 'Roboto',Arial,sans-serif}
.footer-brand{left:82px;top:1097px}
.footer-brand .brand-mark{width:17px;height:20px}
.footer-brand .brand-name{font-size:16px;color:var(--orange)}
.footer-about{left:82px;top:1134px;width:182px;font-size:6.5px;line-height:11px;color:#888}
.footer-col{top:1100px}
.footer-col h4{font-size:13px;font-weight:300;color:var(--white)}
.footer-col .sub{font-size:6.5px;color:var(--orange);margin-top:2px}
.footer-col ul{margin:4px 0 0 2px}
.footer-col li{list-style:none;font-size:6.4px;color:#888;line-height:15px;display:flex;gap:7px;align-items:flex-start;margin-top:3px}
.footer-col li svg{flex:none;margin-top:4px}
.copyright{left:445px;top:1182px;font-size:6.4px;color:#888}
.footer-badges{left:584px;top:1166px;display:flex;gap:4px}
.footer-badges span{width:15px;height:26px;background:#bfbfbf;border-radius:2px}
</style>
</head>
<body>

<header class="site-header abs">
  <div class="brand abs" style="left:55px;top:10px"><span class="brand-mark"></span><span class="brand-name">Kavreo</span></div>
  <nav class="main-nav abs">
    <span>Home</span><span class="sep"></span><span>Torvista</span><span class="sep"></span><span>Portfolio</span><span class="sep"></span><span>Contact</span>
  </nav>
  <div class="header-phone abs"><b>130</b>0 648 907</div>
  <div class="header-icons abs">
    <span><svg width="7" height="7" viewBox="0 0 10 10"><path d="M2 1l2 2-1 1.5c.7 1.2 1.3 1.8 2.5 2.5L7 6l2 2-1.5 1.5C4 9 1 6 .5 2.5z" fill="#fff"/></svg></span>
    <span><svg width="7" height="6" viewBox="0 0 10 8"><rect x=".5" y=".5" width="9" height="7" fill="none" stroke="#fff"/><path d="M.5.5L5 4.5 9.5.5" fill="none" stroke="#fff"/></svg></span>
  </div>
  <div class="header-note abs">Call now for more information OR <a href="#">support@kavreo.example</a></div>
</header>

<section class="hero abs">
  <div class="hero-photo" role="img" aria-label="Photo of a merchant at a wooden desk reviewing sales charts beside an open laptop"></div>
  <h1 class="hero-title abs">Kavreo Commerce</h1>
  <p class="hero-sub abs">Get Started With The World's Leading<br><span>E - Commerce Platform</span></p>
  <div class="hero-dots abs"><span></span><span></span><span></span></div>
  <div class="hero-badges abs" aria-label="Certification badges"><span></span><span></span></div>
</section>

<section class="welcome abs">
  <h2>Welcome To<br><em>Our Kavreo Commerce</em></h2>
  <p>Bravuln is a Melbourne based website development company. We specialise exclusively in Torvista online store development, from in the support</p>
  <ul>
    <li><svg width="6" height="8" viewBox="0 0 6 8"><path d="M0 0l6 5H3l1.5 3-1 .4L2 5.5 0 7z" fill="#0d3c73"/></svg>Your local online store developers</li>
    <li><svg width="6" height="8" viewBox="0 0 6 8"><path d="M0 0l6 5H3l1.5 3-1 .4L2 5.5 0 7z" fill="#0d3c73"/></svg>Torvista specialists</li>
    <li><svg width="6" height="8" viewBox="0 0 6 8"><path d="M0 0l6 5H3l1.5 3-1 .4L2 5.5 0 7z" fill="#0d3c73"/></svg>Torvista Bronze solution partner</li>
  </ul>
</section>

<article class="teaser abs" style="left:291px">
  <h3>Why Bravuln?</h3>
  <p>Fast Torvista-based online stores, built on time and to specification, backed by effective, focused support, means that our clients are among</p>
  <a href="#">Contact Us Now!</a>
</article>
<article class="teaser abs" style="left:402px">
  <h3>Why Torvista?</h3>
  <p>Torvista is the world's leading open source eCommerce platform. No other open-source or free system offers out-of-the-box functionality search</p>
  <a href="#">Read More</a>
</article>
<article class="teaser abs" style="left:513px">
  <h3>What We Do.</h3>
  <p style="text-align:center">From support, maintenance and upgrades to redesigns, migrations and full site builds, we make your online store do what you need it to do.</p>
  <a href="#">Read More</a>
</article>

<section class="services abs">
  <div class="services-accent"></div>
  <div class="services-bg" role="img" aria-label="Dim photo of a person working at a laptop"></div>
  <h2 class="section-title">Our <b>Service</b></h2>
  <article class="service-card abs" style="left:55px">
    <div class="service-photo" role="img" aria-label="Magnifier over a system, audit theme" style="background:radial-gradient(circle at 45% 45%,#e08a3a 0,#c7783a 12%,#7fb2d6 30%,#3d77a8 60%,#16365a 100%)"></div>
    <h3>Torvista System Audit</h3>
    <p>With over 200 stores in Australia and a massive online presense, Lacewell Co were hoping to take the Torvista support and maintenance to the next level.</p>
  </article>
  <article class="service-card abs" style="left:198px">
    <div class="service-photo" role="img" aria-label="Team working over charts on a desk" style="background:radial-gradient(circle at 60% 60%,#e7e2dc 0,#cdbfb0 22%,#a4724c 50%,#6b4428 100%)"></div>
    <h3>Torvista Performance<br>Optimisation</h3>
    <p>Bravuln conducted an inside out system audit of the Torvista Enterprise setup, coming back with a number</p>
  </article>
  <article class="service-card abs" style="left:340px">
    <div class="service-photo" role="img" aria-label="Website shown on several devices" style="background:linear-gradient(180deg,#f2f2f2 0,#e6e6e6 30%,#b9a48a 55%,#6d7480 80%,#f0f0f0 100%)"></div>
    <h3>Torvista Website<br>Emergency Recovery</h3>
    <p>The lead up to Christmas 2014, Bravuln implemented a rewrite of Torvista core Enterprise Edition wishlist function</p>
  </article>
  <article class="service-card abs" style="left:483px">
    <div class="service-photo" role="img" aria-label="Server racks in a data centre" style="background:linear-gradient(90deg,#0e1a2e,#34557f 25%,#18263d 45%,#4a6d99 65%,#101c30 100%)"></div>
    <h3>Torvista Development<br>Infrastructure Hosting</h3>
    <p>The plan was to remove the default Wishlist limitations, add AJAX driven functionality and closely integrate the rest</p>
  </article>
</section>

<section class="clients abs">
  <h2 class="section-title">Our <b>Client</b></h2>
  <div class="client-strip">
    <span>Torvista</span><span>QRX</span><span>DataVane</span><span>NCB</span><span>Quellix</span>
  </div>
</section>

<div class="map abs" role="img" aria-label="Grayscale street map of the office location">
  <svg class="map-pin abs" width="12" height="17" viewBox="0 0 12 17"><path d="M6 0a6 6 0 0 1 6 6c0 4-6 11-6 11S0 10 0 6a6 6 0 0 1 6-6z" fill="#ee8a2a"/><circle cx="6" cy="6" r="2.4" fill="#fff"/></svg>
</div>

<footer class="site-footer abs"></footer>
<form class="newsletter abs">
  <h4>Subscribe <b>Newsletter</b></h4>
  <input type="email" placeholder="Enter The Mail Id">
  <button type="button">Go</button>
</form>
<div class="footer-brand brand abs"><span class="brand-mark"></span><span class="brand-name">Kavreo</span></div>
<p class="footer-about abs">Torvista, fully owned by Nelbay Inc., is one of the most popular eCommerce platforms. It offers flexible, scalable eCommerce solutions designed to help businesses grow and succeed online. The Torvista platform is trusted</p>
<div class="footer-col abs" style="left:330px">
  <h4>Contact Us</h4>
  <div class="sub">Submit online contact form</div>
  <ul>
    <li><svg width="6" height="6" viewBox="0 0 10 10"><path d="M2 1l2 2-1 1.5c.7 1.2 1.3 1.8 2.5 2.5L7 6l2 2-1.5 1.5C4 9 1 6 .5 2.5z" fill="#ee8a2a"/></svg>Call 1300 648 907</li>
    <li><svg width="7" height="5" viewBox="0 0 10 8"><rect x=".5" y=".5" width="9" height="7" fill="none" stroke="#ee8a2a"/><path d="M.5.5L5 4.5 9.5.5" fill="none" stroke="#ee8a2a"/></svg>Email support@kavreo.example</li>
  </ul>
</div>
<div class="footer-col abs" style="left:492px">
  <h4>Address</h4>
  <div class="sub">Submit online contact form</div>
  <ul>
    <li><svg width="5" height="7" viewBox="0 0 12 17"><path d="M6 0a6 6 0 0 1 6 6c0 4-6 11-6 11S0 10 0 6a6 6 0 0 1 6-6z" fill="#ee8a2a"/></svg>Suite 42, Level 3|8 Wattlebrook<br>Lane|Fernvale Heights VIC 3999</li>
  </ul>
</div>
<div class="copyright abs">Copyrights@2016 Kavreo, all rights reserved</div>
<div class="footer-badges abs" aria-label="Certification badges"><span></span><span></span></div>

</body>
</html>
```